Luxury Japanese Matcha Green Tea Packaging Full Packet Design

We're looking for a quality full pack design (front and back) for Ceremonial Grade and Premium Grade Matcha to sell on Bazaarly. We need a 2D versions of front and back images in photoshop and JPG. We also need a 3D versions of front and back for marketing purposes.

You can see our current styling and pack at www.brewvantis.co.uk. However, we want to improve the design and go more professional, simple and elegant with the brand. The last design was from 3 years a go. But hopefully you can see what we are about.

The design will be identical both both packs:

Pack 1: 230mm x 140mm - Premium Grade
Pack 2: 170mm x 120mm - Ceremonial Grade

The design needs to fit both sizes, with pack 1 saying Premium Grade and pack 2 saying Ceremonial Grade.

As many colours as needed, printing is CMYK + White digital printed.

Front of pack:

Product Headline:

Organic Handpicked
Stoneground Japanese Matcha
Green Tea Powder

抹茶

Text: Premium Grade (pack 1) / Ceremonial Grade (pack 2)

100g (pack 1) / 40g (pack 2)

(EU Organic logo)

Back of pack:

Organic Certified GB-ORG-19
Stone Ground Ceremonial Grade Matcha from Uji

Ingredients: 100% Organic Matcha Green Tea Powder

Place of origin: Japan, Store in a cool, dry, dark place
Keep sealed at all times, Best Before 31/03/2020
Not recommended for use if pregnant or nursing

Your next order is ready for you at www.KelpHour.co.uk

Preparing Traditional Matcha Tea:
Sift 1-2g or 1/2 teaspoon of Matcha Green Tea
powder into a bowl or large cup. Add 1/2 cup of hot water
at drinking temperature. Whisk with Bamboo or
Electric Whisk until frothy. Drink immediately.

Preparing Matcha Latte:
Sift 1-2g of Matcha Power into a cup, mix in 2-3 tablespoons of hot water.
Add hot milk and sweetener if desired. Whisk thoroughly.

Nutritional Information:

Per 1g Per 100g
Energy 14.44kJ 1446kJ
3.44kCal 345kCal
Fat 0.04g 4g
Saturates <0.01g 0.6g
Carbohydrates 0.76g 76g
of which sugars 0.47g 47.2g
Protein 0.144g 14.5g
Salt <0.01g 126mg

Per 1g Per 100g
Calcium 1.88mg 191mg
Potassium 94.8mg 3750mg
Iron <0.1g 1.6mg
Zinc <0.1g 1.72mg
Vitamin A 120µg (15% RDA) 2400µg (150% RDA)
Vitamin C 3mg (4% RDA) 60mg (75% RDA)
Folic acid 6µg (6% RDA) 60µg (30% RDA)
Riboflavin 0.1mg (4% RDA) 1.4mg (96% RDA)
Caffeine 17mg 1700mg

Quillon Harbour Ltd. T/A Brewvantis
Company Number: 05617429
Registered Office: 7 The Yard, Darnwick Cl
Newbury, Berkshire, RG17 2QH
social@brewvantis.co.uk
Local Call +44 (0) 20 3184 6057 / Freephone +44 (0) 800 512 7736

This supplement should not be used as a substitute for a varied diet Do not exceed the recommended daily dose.

For more information on Matcha, download the free eBook at www.TheLeafPrimer.com

Please consult a healthcare practitioner if you are pregnant or taking prescription medicine before using this product.

Recommended daily dose

1-5g daily

Storage information: Store in a cool dry place away from sunlight, moisture, and heat. Keep contents dry.

Logos for back of pack:
EU Organic logo with 'GB-ORG-19 Non-EU Agriculture' written directly underneath it.
Vegan logo
Natural Crop Alliance logo
Bazaarly Barcode

Additional deisgn notes:

We have included a design that we like.

The top 2cm will be torn off by the user, so should not contain any key information.

Target Market(s)

High End health and wellness Consumers

Colors
acd036
0455a3
edf8f6

Requirements
Must have
• Stand out on Bazaarly. Show the product to be premium.

```html
<!DOCTYPE html>
<html lang="en">
<head>
<meta charset="utf-8">
<title>Brewvantis Matcha – Front of Pack</title>
<link rel="stylesheet" href="https://fonts.googleapis.com/css2?family=Open+Sans:wght@400;600;700;800&family=Oswald:wght@400&family=Noto+Serif+JP:wght@400&display=swap">
<style>
  :root {
    --backdrop: #ececec;
    --pouch: #ffffff;
    --seal: #f2f2f2;
    --band-dark: #2f302e;
    --band-text: #ffffff;
    --lime: #acd036;
    --lime-deep: #8fb52a;
    --powder-light: #eef5dc;
    --powder: #8cb23a;
    --powder-deep: #6f9a26;
    --olive: #66841c;
    --olive-dark: #4d6a14;
    --ink: #1c1c1c;
    --ink-soft: #333333;
  }
  * { box-sizing: border-box; margin: 0; padding: 0; }
  html, body { width: 1200px; height: 1115px; overflow: hidden; }
  body {
    background: var(--backdrop);
    font-family: "Open Sans", sans-serif;
    position: relative;
  }
  .pouch {
    position: absolute;
    left: 250px; top: 20px;
    width: 700px; height: 1075px;
    background: var(--pouch);
    box-shadow: 0 0 0 1px #dcdcdc;
  }
  .pouch__seal {
    position: absolute; left: 0; right: 0; top: 0; height: 40px;
    background: var(--seal);
    border-bottom: 1px solid #e4e4e4;
  }
  .brand-header {
    position: absolute; left: 210px; top: 0; width: 280px;
  }
  .brand-header__band {
    height: 114px;
    background: var(--band-dark);
    display: flex; align-items: flex-end; justify-content: center;
    padding-bottom: 14px; gap: 8px;
  }
  .brand-header__dot {
    width: 12px; height: 12px; border-radius: 50%;
    background: var(--lime); margin-bottom: 12px;
  }
  .brand-header__name {
    font-size: 38px; font-weight: 400; color: var(--lime);
    line-height: 1;
  }
  .brand-header__tagline {
    height: 34px; background: var(--band-dark);
    border-top: 2px solid #fff;
    color: var(--band-text); font-size: 24px; text-align: center; line-height: 31px;
  }
  .brand-header__origin {
    height: 98px; background: var(--lime);
    border-radius: 0 0 140px 140px / 0 0 98px 98px;
    border-top: 2px solid #fff;
    text-align: center; color: var(--olive-dark);
  }
  .brand-header__stoneground { font-size: 37px; line-height: 1.1; padding-top: 2px; }
  .brand-header__japanese { font-size: 30px; font-weight: 800; line-height: 1; letter-spacing: 1px; }
  .matcha-heart {
    position: absolute; left: 146px; top: 337px; width: 482px; height: 418px;
    border-radius: 24px;
    background: radial-gradient(ellipse at 48% 45%, var(--powder-light) 0%, #ffffff 30%, var(--powder) 78%, var(--powder-deep) 100%);
  }
  .product-name {
    position: absolute; left: 0; width: 714px; top: 448px;
    text-align: center; font-size: 74px; font-weight: 800; color: var(--olive);
    letter-spacing: -1px; line-height: 1;
  }
  .product-kanji {
    position: absolute; left: 0; width: 714px; top: 536px;
    text-align: center; font-family: "Noto Serif JP", serif;
    font-size: 64px; color: var(--ink); line-height: 1;
  }
  .descriptor-box {
    position: absolute; left: 98px; top: 813px; width: 512px; height: 77px;
    border: 2px solid var(--olive-dark);
    display: flex; align-items: center; justify-content: center;
    font-size: 27px; font-weight: 700; color: var(--olive-dark);
    letter-spacing: 11px; padding-left: 11px;
  }
  .connector-vertical {
    position: absolute; left: 363px; top: 890px; width: 2px; height: 120px;
    background: var(--olive-dark);
  }
  .connector-base {
    position: absolute; left: 300px; top: 1008px; width: 130px; height: 2px;
    background: var(--olive-dark);
  }
  .grade {
    position: absolute; left: 97px; top: 938px;
    font-size: 24px; font-weight: 700; color: var(--ink-soft); letter-spacing: 2.5px;
  }
  .certification {
    position: absolute; left: 432px; top: 930px;
    display: flex; align-items: center; gap: 8px;
  }
  .certification__badge { width: 46px; height: 32px; background: var(--lime-deep); }
  .certification__text {
    font-family: "Oswald", sans-serif; font-size: 14px; line-height: 1.3;
    color: var(--ink-soft); text-transform: uppercase;
  }
  .net-weight {
    position: absolute; left: 0; width: 730px; top: 1019px;
    text-align: center; font-size: 19px; color: var(--ink-soft);
  }
</style>
</head>
<body>
  <main class="pouch">
    <div class="pouch__seal"></div>

    <header class="brand-header">
      <div class="brand-header__band">
        <span class="brand-header__dot"></span>
        <span class="brand-header__name">Brewvantis</span>
      </div>
      <div class="brand-header__tagline">Organic Handpicked</div>
      <div class="brand-header__origin">
        <div class="brand-header__stoneground">Stoneground</div>
        <div class="brand-header__japanese">JAPANESE</div>
      </div>
    </header>

    <div class="matcha-heart" role="img" aria-label="Photograph of green matcha powder scattered in a heart shape"></div>

    <h1 class="product-name">MATCHA</h1>
    <p class="product-kanji" lang="ja">抹茶</p>

    <div class="descriptor-box">GREEN TEA POWDER</div>
    <div class="connector-vertical"></div>
    <div class="connector-base"></div>

    <p class="grade">PREMIUM GRADE</p>

    <div class="certification">
      <span class="certification__badge"></span>
      <p class="certification__text">Acquired EU<br>Organic Certification</p>
    </div>

    <p class="net-weight">NET&nbsp; WT. 100G</p>
  </main>
</body>
</html>
```